Heating and Cooling Company mobile website

We need a website specifically designed for a viewing on a mobile device.

We serve the northern New Jersey heating, cooling and electrical residential market.

The goal is the drive traffic to the site by using Brintel Pay Per click. People will be searching for an HVAC contractor, and they land on our page. They need to get key info quickly without all the clutter of a desktop type of site.

Target Market(s)

Homeowners

Industry/Entity Type

Hvac

Coding

Coded - Design and coding required

Number of Pages Required

5+ page

Font styles to use
Serif

Requirements
Must have
• View attachments to see samples of the desktop version. It must have a similar color scheme
• The copy of the website is also attached
Nice to have
• Would like it to have a sort of Vardok feel to it. Make it seem like its an app that people are using and that its exciting to be on the website. It would be nice to have a page where customers can book appointments

```html
<!DOCTYPE html>
<html lang="en">
<head>
<meta charset="utf-8">
<title>Hearthwell Climate – Heating &amp; Cooling</title>
<link rel="stylesheet" href="https://fonts.googleapis.com/css2?family=Merriweather:wght@700;900&family=Lato:wght@400;700&family=Tinos&family=Oswald:wght@500&display=swap">
<style>
  :root {
    --maroon: #8a1727;
    --maroon-deep: #6c0f1d;
    --orange: #f07a22;
    --gold: #f4b23a;
    --cream: #f3e7cf;
    --sand: #e6dfcf;
    --mist: #efecef;
    --ink: #2b2f45;
    --label: #2f2f38;
    --white: #ffffff;
  }
  * { box-sizing: border-box; margin: 0; padding: 0; }
  html, body { width: 1200px; height: 3805px; overflow: hidden; background: var(--white); }
  body { font-family: "Lato", Arial, sans-serif; }
  .site { width: 1200px; height: 3805px; display: flex; flex-direction: column; }

  .masthead { height: 204px; background: var(--maroon); display: flex; align-items: center; justify-content: center; gap: 22px; }
  .brand-dot { width: 30px; height: 30px; border-radius: 50%; background: var(--orange); }
  .brand-name { font-family: "Merriweather", Georgia, serif; font-weight: 900; font-size: 58px; color: var(--cream); letter-spacing: 1px; }

  .hero-photo { height: 648px; background: linear-gradient(180deg, #bdb2a2 0%, #a99d8b 45%, #7a1a26 62%, #3a2a2a 80%, #c9c1b4 100%); }

  .trust { height: 642px; background: var(--sand); display: flex; flex-direction: column; align-items: center; padding-top: 62px; }
  .trust-title { font-family: "Merriweather", Georgia, serif; font-weight: 700; color: var(--ink); font-size: 84px; line-height: 118px; text-align: center; }
  .learn-more { margin-top: 58px; width: 380px; height: 170px; position: relative; display: flex; flex-direction: column; align-items: center; justify-content: center; color: var(--white); font-weight: 700; font-size: 32px; letter-spacing: 1px; text-decoration: none; }
  .learn-more svg.frame { position: absolute; inset: 0; }
  .learn-more span { position: relative; }
  .learn-more .chev { position: relative; margin-top: 8px; }

  .services { height: 1080px; background: var(--mist); display: grid; grid-template-columns: 1fr 1fr; padding: 50px 90px 0; }
  .service { display: flex; flex-direction: column; align-items: center; }
  .badge { width: 430px; height: 350px; position: relative; }
  .badge svg { width: 100%; height: 100%; }
  .badge-shadow { width: 380px; height: 22px; border-radius: 50%; background: radial-gradient(ellipse, rgba(0,0,0,0.22), rgba(0,0,0,0) 70%); margin-top: -6px; }
  .service-label { margin-top: 46px; font-weight: 700; font-size: 33px; color: var(--label); letter-spacing: 0.5px; }

  .sitemap { height: 751px; background: var(--maroon); display: grid; grid-template-columns: 470px 1fr; padding: 58px 0 0 157px; color: var(--white); font-size: 30px; line-height: 40px; }
  .sitemap ul { list-style: none; margin-bottom: 40px; }
  .sitemap .strong { font-weight: 700; }

  .contact { height: 335px; background: var(--maroon-deep); position: relative; display: grid; grid-template-columns: 600px 1fr; align-items: center; color: var(--white); }
  .address { text-align: center; font-size: 30px; line-height: 43px; padding-top: 20px; }
  .connect { display: flex; flex-direction: column; align-items: center; padding-top: 10px; padding-right: 60px; }
  .connect-title { font-family: "Oswald", "Arial Narrow", sans-serif; font-weight: 500; font-size: 44px; margin-bottom: 28px; }
  .ribbon { width: 420px; height: 118px; }
  .to-top { position: absolute; top: -44px; right: 40px; width: 80px; height: 80px; border-radius: 50%; background: var(--orange); border: 5px solid var(--cream); display: flex; align-items: center; justify-content: center; }

  .legal { height: 145px; background: var(--maroon-deep); padding: 0 84px; }
  .legal-rule { height: 2px; background: rgba(255,255,255,0.12); }
  .legal p { font-family: "Tinos", "Times New Roman", serif; color: var(--white); font-size: 36px; padding-top: 42px; }
</style>
</head>
<body>
<div class="site">
  <header class="masthead">
    <span class="brand-dot"></span>
    <span class="brand-name">HEARTHWELL CLIMATE</span>
  </header>

  <div class="hero-photo" role="img" aria-label="Photo of a smiling family behind a company service van"></div>

  <section class="trust">
    <h1 class="trust-title">Most Trusted<br>Heating &amp; Cooling<br>Company</h1>
    <a class="learn-more" href="#">
      <svg class="frame" viewBox="0 0 380 170" preserveAspectRatio="none">
        <path d="M60 12 Q190 0 320 12 Q332 40 360 48 Q374 85 360 122 Q332 130 320 158 Q190 170 60 158 Q48 130 20 122 Q6 85 20 48 Q48 40 60 12Z" fill="#8a1727" stroke="#f07a22" stroke-width="9"/>
      </svg>
      <span>LEARN MORE</span>
      <svg class="chev" width="16" height="22" viewBox="0 0 16 22"><path d="M3 3 L12 11 L3 19" fill="none" stroke="#fff" stroke-width="4"/></svg>
    </a>
  </section>

  <section class="services">
    <div class="service">
      <div class="badge">
        <svg viewBox="0 0 200 165">
          <path d="M32 10 Q100 -4 168 10 Q170 30 190 36 Q200 82 190 128 Q170 134 168 155 Q100 169 32 155 Q30 134 10 128 Q0 82 10 36 Q30 30 32 10Z" fill="#8a1727" stroke="#f07a22" stroke-width="7"/>
          <g fill="#f3e7cf" stroke="#f3e7cf" stroke-width="5" stroke-linecap="round">
            <circle cx="100" cy="82" r="18" stroke="none"/>
            <line x1="100" y1="44" x2="100" y2="56"/><line x1="100" y1="108" x2="100" y2="120"/>
            <line x1="62" y1="82" x2="74" y2="82"/><line x1="126" y1="82" x2="138" y2="82"/>
            <line x1="73" y1="55" x2="81" y2="63"/><line x1="119" y1="101" x2="127" y2="109"/>
            <line x1="127" y1="55" x2="119" y2="63"/><line x1="81" y1="101" x2="73" y2="109"/>
          </g>
        </svg>
      </div>
      <div class="badge-shadow"></div>
      <div class="service-label">HEATING</div>
    </div>
    <div class="service">
      <div class="badge">
        <svg viewBox="0 0 200 165">
          <path d="M32 10 Q100 -4 168 10 Q170 30 190 36 Q200 82 190 128 Q170 134 168 155 Q100 169 32 155 Q30 134 10 128 Q0 82 10 36 Q30 30 32 10Z" fill="#8a1727" stroke="#f07a22" stroke-width="7"/>
          <g stroke="#f3e7cf" stroke-width="5" stroke-linecap="round" fill="none">
            <line x1="100" y1="46" x2="100" y2="118"/>
            <line x1="69" y1="64" x2="131" y2="100"/>
            <line x1="69" y1="100" x2="131" y2="64"/>
            <path d="M92 52 L100 60 L108 52 M92 112 L100 104 L108 112"/>
            <path d="M72 74 L82 70 L78 60 M128 90 L118 94 L122 104"/>
            <path d="M72 90 L82 94 L78 104 M128 74 L118 70 L122 60"/>
          </g>
        </svg>
      </div>
      <div class="badge-shadow"></div>
      <div class="service-label">AIR CONDITIONING</div>
    </div>
    <div class="service">
      <div class="badge">
        <svg viewBox="0 0 200 165">
          <path d="M32 10 Q100 -4 168 10 Q170 30 190 36 Q200 82 190 128 Q170 134 168 155 Q100 169 32 155 Q30 134 10 128 Q0 82 10 36 Q30 30 32 10Z" fill="#8a1727" stroke="#f07a22" stroke-width="7"/>
          <g stroke="#f3e7cf" stroke-width="5" fill="none" stroke-linecap="round">
            <path d="M84 48 H124 V118 H84 Z"/>
            <line x1="94" y1="62" x2="114" y2="62"/>
            <line x1="94" y1="74" x2="114" y2="74"/>
            <path d="M58 84 Q70 76 82 84 T106 84 T130 84"/>
            <path d="M58 98 Q70 90 82 98 T106 98 T130 98"/>
          </g>
        </svg>
      </div>
      <div class="badge-shadow"></div>
      <div class="service-label">OTHER SERVICES</div>
    </div>
    <div class="service">
      <div class="badge">
        <svg viewBox="0 0 200 165">
          <path d="M32 10 Q100 -4 168 10 Q170 30 190 36 Q200 82 190 128 Q170 134 168 155 Q100 169 32 155 Q30 134 10 128 Q0 82 10 36 Q30 30 32 10Z" fill="#8a1727" stroke="#f07a22" stroke-width="7"/>
          <rect x="62" y="50" width="76" height="66" rx="10" fill="#f3e7cf" role="img" aria-label="Icon of the customers we serve"/>
        </svg>
      </div>
      <div class="badge-shadow"></div>
      <div class="service-label">WHO WE SERVICE</div>
    </div>
  </section>

  <nav class="sitemap">
    <div>
      <ul class="strong"><li>Home</li><li>About</li><li>Services</li><li>Testimonials</li><li>Blog</li><li>Contact</li></ul>
      <ul><li class="strong">Heating</li><li>New Installation</li><li>Repair &amp; Service</li><li>Heat Pumps</li><li>Boilers</li><li>Radiant Heat Systems</li></ul>
    </div>
    <div>
      <ul><li class="strong">Air Conditioning</li><li>New Installation</li><li>Repair &amp; Service</li><li>Ductless Systems</li></ul>
      <ul><li class="strong">Other Services</li><li>Indoor Air Quality</li><li>Thermostats &amp; Zoning</li><li>Generators</li><li>Products</li></ul>
      <ul><li class="strong">Who We Service</li><li>Residential &amp; Homeowners</li><li>Commercial Businesses</li></ul>
    </div>
  </nav>

  <section class="contact">
    <a class="to-top" href="#" aria-label="Back to top">
      <svg width="30" height="20" viewBox="0 0 30 20"><path d="M4 16 L15 5 L26 16" fill="none" stroke="#fff" stroke-width="5"/></svg>
    </a>
    <address class="address" style="font-style:normal">
      24 Linden Court<br>Maple Ridge, NJ 07000<br>555.010.2040<br>hello@hearthwellclimate.com
    </address>
    <div class="connect">
      <div class="connect-title">Stay Connected</div>
      <svg class="ribbon" viewBox="0 0 420 118">
        <path d="M0 6 H420 L396 59 L420 112 H0 L24 59 Z" fill="#f07a22"/>
        <circle cx="138" cy="59" r="34" fill="#fff"/>
        <circle cx="210" cy="59" r="34" fill="#fff"/>
        <circle cx="282" cy="59" r="34" fill="#fff"/>
      </svg>
    </div>
  </section>

  <footer class="legal">
    <div class="legal-rule"></div>
    <p>© 2017 Company Name.&nbsp; All right reserved.&nbsp; Term of Use</p>
  </footer>
</div>
</body>
</html>
```